Website for a company offering full serivce charging solutions for electric cars

The company "tanu-werk" (english: "tanu-works") offering all-in-one-solutions for charging infrastructure for electric mobility.

There are four products:
1- Wallboxes for single-family homes
2- Solutions for property devloper/-management for property parking space
3- All-in-one-charging solution for municipalities/communities
4- Solutions for tourism/hotels/holiday appartments

The Website structure:
1. Main Page
2.1. Product Page Single Homes
2.2. Product Page Property Management / Parking
2.3. Product Page Municipality
2.4. Product Page Tourism
3. Contact Form / Request for information
4. Imprint / Legal

The Website should be built on Wordpress with a powerful possibility to simply add/modify specific landing pages.

We would like you to implement the website later and also maintain it if possible, but we would be able to do minor modifications by ourselfs (for A/B-Testing)

The website should be clear and simple, easy to understand.
Target group is mainly B2C without deeper knowledge of that topic.

It should suggest, that we will provide a very simple way to get the charging infrastructure done.

We need a contact form, maybe we will use Hubspot later.

Attached you will find a draft of the main page and a landing page (for 2.2) - it is just the content, please ignore the design. We would love to let you create a suitable design.
Also you will find some drafts a bit different for the same story.

I added also a few stock photos, but they don't need to be used! If you have better ideas, you are welcome!

Industry/Entity Type

Charging/Electric mobility

Number of Pages Required

2 page

Font styles to use
Sans Serif

Requirements
Must have
• Based on Wordpress, and the designer should be able to implement it on Wordpress on a later step

```html
<!DOCTYPE html>
<html lang="de">
<head>
<meta charset="utf-8">
<title>tanu-werk – einfach mehr als laden</title>
<link rel="stylesheet" href="https://fonts.googleapis.com/css2?family=Titillium+Web:wght@300;400;600;700&family=Raleway:wght@400;500;600;700&display=swap">
<style>
:root{
  --bg:#151b28;
  --bg-deep:#121826;
  --band:#13223a;
  --pink:#e0249a;
  --magenta:#c42ab8;
  --purple:#8a4fc8;
  --violet:#6b3fc0;
  --text:#ffffff;
  --muted:#c9cdd6;
  --soft:#a9afbd;
}
*{box-sizing:border-box;margin:0;padding:0}
html,body{width:1200px;height:4222px;overflow:hidden;background:var(--bg);color:var(--text);font-family:"Raleway",sans-serif}
.page{position:relative;width:1200px;height:4222px}
section,header,footer{position:absolute;left:0;width:1200px}

/* header */
.site-header{top:0;height:93px;background:var(--bg)}
.brand{position:absolute;left:103px;top:18px;display:flex;align-items:center;gap:14px}
.brand-dot{width:40px;height:40px;border-radius:50%;background:var(--pink)}
.brand-name{font-family:"Titillium Web",sans-serif;font-weight:600;font-size:26px;line-height:1;color:#fff}
.brand-tag{font-size:13px;color:var(--muted);margin-top:3px}
.nav a{position:absolute;top:28px;font-size:14px;letter-spacing:.3px;color:#fff;text-decoration:none;font-family:"Raleway",sans-serif}
.nav .active::after{content:"";position:absolute;left:0;right:0;bottom:-12px;height:3px;background:var(--pink)}
.nav .cta{top:21px;left:947px;width:146px;height:38px;border-radius:19px;background:linear-gradient(90deg,var(--purple),var(--pink));display:flex;align-items:center;justify-content:center;font-weight:700;font-size:14px}

/* hero */
.hero{top:93px;height:599px;overflow:hidden}
.hero-bg{position:absolute;inset:0;background:linear-gradient(90deg,#1a2030 0%,#2a2540 35%,#6b3a7a 60%,#3a2450 100%)}
.hero-visual{position:absolute;left:560px;top:0;width:630px;height:599px;border-radius:0 300px 300px 340px;background:radial-gradient(circle at 60% 45%,#f3a0f0 0%,#c65ad8 35%,#8a3fb8 70%,#5a2e86 100%)}
.hero-copy{position:absolute;left:115px;top:122px}
.hero h1{font-family:"Titillium Web",sans-serif;font-size:60px;line-height:56px;font-weight:700}
.hero h1 .light{font-weight:300;display:block}
.hero p{margin-top:18px;font-size:20px;line-height:30px;color:#eee;width:460px}
.btn-more{display:inline-flex;align-items:center;justify-content:center;margin-top:30px;width:193px;height:50px;border-radius:25px;background:linear-gradient(90deg,var(--violet),var(--pink));font-weight:700;font-size:15px;color:#fff;text-decoration:none}

/* intro */
.intro{top:692px;height:570px;text-align:center}
.intro-visual{position:absolute;left:220px;top:170px;width:980px;height:400px;background:radial-gradient(ellipse at 55% 60%,#2f3a48 0%,#1d2532 45%,var(--bg) 75%);opacity:.9}
.bolt{display:block;margin:0 auto}
.intro .bolt{position:absolute;left:588px;top:76px}
.intro h2{position:absolute;left:200px;top:128px;width:800px;font-size:21px;line-height:33px;font-weight:600}
.intro p{position:absolute;left:170px;top:245px;width:860px;font-size:16px;line-height:26px;color:var(--muted)}

/* ask */
.ask{top:1262px;height:213px;text-align:center}
.ask .bolt{position:absolute;left:602px;top:16px}
.ask h2{position:absolute;left:0;width:1200px;top:76px;font-family:"Titillium Web",sans-serif;font-weight:600;font-size:31px;line-height:34px;text-transform:uppercase}
.ask h2 span{display:block;font-weight:300}

/* segments */
.seg-title{font-family:"Titillium Web",sans-serif;font-size:36px;font-weight:300;line-height:1;text-transform:uppercase}
.seg-title b{color:var(--pink);font-weight:700}
.seg-title::after{content:"";display:block;width:52px;height:2px;background:#fff;margin-top:12px}
.ring{position:absolute}
.ring-photo{position:absolute;border-radius:50%}

.private{top:1475px;height:549px}
.private .ring{left:110px;top:20px}
.private .ring-photo{left:148px;top:60px;width:396px;height:396px;background:radial-gradient(circle at 55% 45%,#e6f2ff 0%,#7fb6f0 35%,#2a63c4 70%,#17305e 100%)}
.private .copy{position:absolute;left:624px;top:44px;width:500px}
.plain-list{list-style:none;margin-top:26px}
.plain-list li{font-size:13px;line-height:16px;color:#e2e4ea;margin-bottom:8px}

.business{top:2024px;height:677px;background:var(--band);overflow:hidden}
.business-visual{position:absolute;left:590px;top:330px;width:610px;height:347px;background:radial-gradient(ellipse at 45% 50%,#3b55c8 0%,#1f2f80 35%,var(--band) 75%)}
.business .seg-title{position:absolute;left:0;width:1200px;top:62px;text-align:center}
.business .seg-title::after{margin:12px auto 0}
.arrow-list{list-style:none}
.arrow-list li{position:relative;padding-left:16px;font-size:13px;line-height:25px;font-weight:600;color:#eef0f5}
.arrow-list li::before{content:"";position:absolute;left:1px;top:9px;width:6px;height:6px;border-right:2px solid #fff;border-top:2px solid #fff;transform:rotate(45deg)}
.arrow-list .sub{margin:8px 0 8px 12px}
.arrow-list .sub li{font-weight:500;line-height:19px}
.arrow-list .gap{margin-top:10px}
.business .col-left{position:absolute;left:120px;top:160px;width:480px}
.business .col-right{position:absolute;left:644px;top:170px;width:460px}
.business .col-right li{margin-bottom:9px}

.municipal{top:2701px;height:741px}
.municipal .ring{left:100px;top:105px}
.municipal .ring-photo{left:150px;top:155px;width:390px;height:390px;background:radial-gradient(circle at 50% 45%,#8fb6ff 0%,#3860d0 40%,#1a2a7a 75%,#131a40 100%)}
.municipal .copy{position:absolute;left:626px;top:96px;width:520px}
.pink-list{list-style:none;margin-top:22px}
.pink-list li{position:relative;padding-left:18px;font-size:13px;line-height:17px;color:#e2e4ea;margin-bottom:10.5px}
.pink-list li::before{content:"";position:absolute;left:1px;top:5px;width:5px;height:5px;border-right:2px solid var(--pink);border-top:2px solid var(--pink);transform:rotate(45deg)}

/* contact */
.contact{top:3442px;height:538px;background:linear-gradient(90deg,#4a2a9a 0%,#8b22a8 45%,#d41f8e 80%,#e43a9a 100%);overflow:hidden}
.contact-visual{position:absolute;inset:0;background:radial-gradient(ellipse at 20% 70%,rgba(40,20,90,.55) 0%,transparent 55%),radial-gradient(ellipse at 85% 40%,rgba(255,140,200,.3) 0%,transparent 50%)}
.contact h2{position:absolute;left:0;width:1200px;top:110px;text-align:center;font-family:"Titillium Web",sans-serif;font-weight:300;font-size:40px;line-height:1}
.contact h2 b{font-weight:700}
.contact h2::after{content:"";display:block;width:70px;height:2px;background:#fff;margin:10px auto 0}
.field{position:absolute;left:198px;width:404px;height:53px;background:#fff;border-radius:2px;display:flex;align-items:center;gap:10px;padding-left:20px;font-size:13px;color:#555}
.field svg{flex:none}
.field.message{left:610px;top:189px;width:406px;height:175px;align-items:flex-start;padding-top:18px}
.btn-submit{position:absolute;left:511px;top:388px;width:194px;height:50px;background:#14193a;border-radius:3px;display:flex;align-items:center;justify-content:center;font-weight:700;font-size:16px;color:#fff}

/* footer */
.site-footer{top:3980px;height:242px;background:var(--bg-deep);text-align:center}
.footer-brand{position:absolute;left:0;width:1200px;top:36px;display:flex;justify-content:center;align-items:center;gap:12px}
.footer-brand .brand-dot{width:30px;height:30px}
.footer-nav{position:absolute;top:104px;left:0;width:1200px}
.footer-nav a{position:absolute;font-size:15px;color:#fff;text-decoration:none;transform:translateX(-50%);white-space:nowrap}
.copyright{position:absolute;top:139px;left:0;width:1200px;font-size:13px;color:var(--soft)}
.social{position:absolute;top:178px;left:0;width:1200px;display:flex;justify-content:center;gap:8px}
.social span{width:31px;height:31px;border-radius:50%;background:linear-gradient(135deg,var(--purple),var(--pink))}
</style>
</head>
<body>
<div class="page">

<header class="site-header">
  <div class="brand">
    <span class="brand-dot"></span>
    <div>
      <div class="brand-name">tanu-werk.de</div>
      <div class="brand-tag">einfach mehr als laden</div>
    </div>
  </div>
  <nav class="nav">
    <a class="active" style="left:430px">LÖSUNGEN</a>
    <a style="left:558px">UNTERNEHMEN</a>
    <a style="left:720px">SERVICES</a>
    <a style="left:838px">KARRIERE</a>
    <a class="cta">KONTAKT</a>
  </nav>
</header>

<section class="hero">
  <div class="hero-bg" role="img" aria-label="Dunkle Landschaft mit Ladesymbolen im Hintergrund"></div>
  <div class="hero-visual" role="img" aria-label="Elektroauto beim Laden mit Ladestecker, in Pink und Violett getönt"></div>
  <div class="hero-copy">
    <h1>tanu-werk ist <span class="light">Ihr Partner</span></h1>
    <p>wenn das Laden nicht nur einfach, sondern die Umsetzung auch aus einer Hand kommen soll</p>
    <a class="btn-more">LEARN MORE</a>
  </div>
</section>

<section class="intro">
  <div class="intro-visual" role="img" aria-label="Weißes Elektroauto an einer Ladesäule im Dunkeln"></div>
  <svg class="bolt" width="28" height="42" viewBox="0 0 28 42"><path d="M17 1 3 24h10l-3 17 15-24H15z" fill="none" stroke="var(--purple)" stroke-width="2" stroke-linejoin="round"/></svg>
  <h2>Wir&nbsp; bieten Lösungen sowohl für Privatkunden, Geschäftskunden als auch Kommunen an, die schnell, fair und ohne Eigenleistung zu einer smarten Ladelösung für E-Fahrzeuge kommen möchten.</h2>
  <p>Von der Beratung, über die Installation, Inbetriebnahme bis zur Abrechnung und Wartung bekommen Sie bei tanu-werk alles aus einer Hand. Auf Wunsch vermieten wir auch die Ladetechnik und übernehmen im gewerblichen Bereich die direkte Abrechnung mit dem Nutzer. Für Kommunen bieten wir den kostenfreien Full-Service an und beteiligen die Gemeinden an der Nutzung der Infrastruktur.</p>
</section>

<section class="ask">
  <svg class="bolt" width="28" height="42" viewBox="0 0 28 42"><path d="M17 1 3 24h10l-3 17 15-24H15z" fill="none" stroke="var(--purple)" stroke-width="2" stroke-linejoin="round"/></svg>
  <h2>Fragen Sie uns nach der auf Ihre individuellen <span>Bedürfnisse zugeschnittenen Lösung:</span></h2>
</section>

<section class="private">
  <svg class="ring" width="470" height="470" viewBox="0 0 470 470">
    <circle cx="234" cy="234" r="212" fill="#1c2434"/>
    <path d="M120 40 A212 212 0 0 1 446 232" fill="none" stroke="var(--pink)" stroke-width="9" stroke-linecap="round"/>
    <path d="M22 234 A212 212 0 0 0 380 388" fill="none" stroke="var(--purple)" stroke-width="6" stroke-linecap="round"/>
  </svg>
  <div class="ring-photo" role="img" aria-label="Ladestecker in einer blau leuchtenden Ladebuchse"></div>
  <div class="copy">
    <h2 class="seg-title">Als <b>Privatkunde</b></h2>
    <ul class="plain-list">
      <li>Bestandsanalyse mit umfangreicher Beratung über die Möglichkeiten der Umsetzung</li>
      <li>Prüfung und Übernahme der Anmeldung verfügbarer Fördermöglichkeiten</li>
      <li>Auswahl an smarten Wallbox Lösungen, passend für Ihr Fahrzeug und Ihre Bedürfnisse</li>
      <li>Installation inkl. aller notwendigen Materialien und Tätigkeiten (Durchbrüche, Erdarbeiten, etc.)</li>
      <li>Inbetriebnahme und Einweisung in die Ladetechnik</li>
      <li>Jährlich technische Wartung nach DGUV3</li>
      <li>Reparaturservice, unter Berücksichtigung der geltenden Garantie Ansprüche</li>
      <li>Installation inkl. aller notwendigen Materialien und Tätigkeiten (Durchbrüche, Erdarbeiten, etc.</li>
      <li>Inbetriebnahme und Einweisung in die Ladetechnik</li>
      <li>Jährlich technische Wartung nach DGUV3</li>
      <li>Reparaturservice, unter Berücksichtigung der geltenden Garantie Ansprüche</li>
    </ul>
  </div>
</section>

<section class="business">
  <div class="business-visual" role="img" aria-label="Leuchtender blauer Ladestecker vor digitalem Hintergrund"></div>
  <h2 class="seg-title">Als <b>Geschäftskunde</b></h2>
  <ul class="arrow-list col-left">
    <li>Durchführung einer individuellen Bedarfsanalyse inkl. Ermittlung der</li>
    <li>Anforderungen für:
      <ul class="arrow-list sub">
        <li>Haus- und Immobilienverwaltungen</li>
        <li>Dienstleistungs- und Handelsunternehmen</li>
        <li>Hotel und Beherbergungsbetriebe</li>
        <li>Parkraum- und Parkhausbetreiber</li>
        <li>Tourismus, Sport- und Freizeiteinrichtungen</li>
      </ul>
    </li>
    <li>Planung und Projektierung des Installationsaufwands inkl.</li>
    <li>Materialverbrauch</li>
    <li class="gap">Leasing oder Kauf der Hardware</li>
    <li class="gap">Normgerechte Installation der Ladeinfrastruktur inkl. Durchbruch-,</li>
    <li>Brandschutz- und Erdarbeiten</li>
    <li class="gap">Unterstützung bei der mtl. Nutzungsabrechnung und Einbindung in Ihre vorhandene Abrechnungssysteme</li>
    <li class="gap">ODER direkte Abrechnung mit den Nutzern</li>
  </ul>
  <ul class="arrow-list col-right">
    <li>Bei Bestandsbauten Integration der Ladeinfrastruktur in die</li>
    <li>Gebäudesystemtechnik und ggf. Anpassung des Netzanschlusses</li>
    <li>Inbetriebnahme der Anlage inkl. Prüf- und Messprotokollen</li>
    <li>Wiederkehrende technische Prüfung der Anlage nach DGUV 3</li>
    <li>Austausch und Reparatur Service</li>
  </ul>
</section>

<section class="municipal">
  <svg class="ring" width="490" height="490" viewBox="0 0 490 490">
    <circle cx="245" cy="245" r="222" fill="#1c2434"/>
    <path d="M40 190 A222 222 0 0 1 330 40" fill="none" stroke="var(--pink)" stroke-width="9" stroke-linecap="round"/>
    <path d="M120 430 A222 222 0 0 0 466 250" fill="none" stroke="var(--purple)" stroke-width="6" stroke-linecap="round"/>
  </svg>
  <div class="ring-photo" role="img" aria-label="Digital leuchtendes Elektroauto mit Ladekabel über einer Hand und Stadtsilhouette"></div>
  <div class="copy">
    <h2 class="seg-title">Als <b>Kommune</b></h2>
    <ul class="pink-list">
      <li>Konzeptionierung möglicher Ladeinfrastrukturen innerhalb Ihrer Gemeinde</li>
      <li>Planung und Projektsteuerung inkl. sämtlicher behördlicher Genehmigungsverfahren und Beantragung von Fördermitteln</li>
      <li>Fachgerechte Insttallation und Inbetriebnahme</li>
      <li>Regelmäßige Wartung gemäß Vorschrif</li>
      <li>Reparatur und Kundenservice</li>
      <li>Direkte Abrechnung mit dem Nutzer</li>
      <li>Beteiligung der Gemeinde am Umsatz</li>
      <li>Möglichkeit der Integration von Bonusprogrammen, mit denen der lokale Einzelhandel beworben wird</li>
      <li>von Fördermitteln<br>Fachgerechte Installation und Inbetriebnahme</li>
      <li>Regelmäßige Wartung gemäß Vorschrif</li>
      <li>Reparatur und Kundenservice</li>
      <li>Direkte Abrechnung mit dem Nutzer</li>
      <li>Beteiligung der Gemeinde am Umsatz</li>
      <li>Möglichkeit der Integration von Bonusprogrammen, mit denen der lokale Einzelhandel beworben wird</li>
    </ul>
  </div>
</section>

<section class="contact">
  <div class="contact-visual" role="img" aria-label="Elektroauto an einer Ladestation in Violett- und Pinktönen"></div>
  <h2>CONTACT <b>US</b></h2>
  <div class="field" style="top:189px"><svg width="16" height="16" viewBox="0 0 16 16"><circle cx="8" cy="5" r="3.5" fill="none" stroke="#777" stroke-width="1.3"/><path d="M1.5 15c0-4 3-6 6.5-6s6.5 2 6.5 6" fill="none" stroke="#777" stroke-width="1.3"/></svg>Your Name*</div>
  <div class="field" style="top:249px"><svg width="18" height="14" viewBox="0 0 18 14"><rect x="1" y="1" width="16" height="12" fill="none" stroke="#777" stroke-width="1.3"/><path d="M1 1l8 7 8-7" fill="none" stroke="#777" stroke-width="1.3"/></svg>Email address*</div>
  <div class="field" style="top:310px"><svg width="16" height="16" viewBox="0 0 16 16"><path d="M3 1l3 3-2 2c1 2 3 4 5 5l2-2 3 3-2 3C7 15 1 9 1 3z" fill="none" stroke="#777" stroke-width="1.3" stroke-linejoin="round"/></svg>Phone number*</div>
  <div class="field message">Leave Message</div>
  <div class="btn-submit">SUBMIT NOW</div>
</section>

<footer class="site-footer">
  <div class="footer-brand"><span class="brand-dot"></span><span class="brand-name">tanu-werk</span></div>
  <nav class="footer-nav">
    <a style="left:227px">AGB</a>
    <a style="left:394px">DATENSCHUTZERKLÄRUNG</a>
    <a style="left:594px">IMPRESSUM</a>
    <a style="left:728px">KONTAKT</a>
    <a style="left:853px">KARRIERE</a>
    <a style="left:964px">FAQS</a>
  </nav>
  <div class="copyright">© 2022 tanu-werk GmbH |&nbsp; All Right Reserved</div>
  <div class="social" aria-label="Soziale Netzwerke"><span></span><span></span><span></span><span></span></div>
</footer>

</div>
</body>
</html>
```